Real Estate Website

Please refer to the attached document. It will be for a real estate agency specialising in commercial and residential sales. looking for Modern and minimalist, Sleek, professional, premium feel

```html
<!DOCTYPE html>
<html lang="en">
<head>
<meta charset="utf-8">
<title>Marlowe Group — Commercial, Industrial & Residential Property</title>
<link rel="stylesheet" href="https://fonts.googleapis.com/css2?family=Outfit:wght@500;600;700&family=Poppins:wght@400;500;600&display=swap">
<style>
:root{
  --orange:#ef532a;
  --orange-soft:#f47a4f;
  --navy:#263440;
  --navy-deep:#1e2a35;
  --ink:#1d2630;
  --muted:#6b7480;
  --line:#dfe3e7;
  --paper:#ffffff;
  --mist:#f4f5f6;
}
*{box-sizing:border-box;margin:0;padding:0}
html,body{width:1200px;height:4959px;overflow:hidden}
body{position:relative;font-family:"Poppins",sans-serif;color:var(--ink);background:var(--paper);font-size:13px}
.abs{position:absolute}
h1,h2,h3,h4{font-family:"Outfit",sans-serif}
.btn{position:absolute;display:flex;align-items:center;justify-content:center;gap:8px;background:var(--orange);color:#fff;font-size:12px;font-weight:500;border-radius:3px}
.wordmark{font-family:"Outfit",sans-serif;font-weight:700;color:var(--ink);display:flex;align-items:center;gap:8px;font-size:28px}
.wordmark .dot{width:18px;height:18px;border-radius:50%;background:var(--orange)}

/* header */
.site-header{position:absolute;top:0;left:0;width:1200px;height:102px;background:#fff}
.site-header .wordmark{position:absolute;left:96px;top:32px}
.main-nav{position:absolute;left:338px;top:44px;display:flex;gap:31px;font-size:12px;font-weight:500;letter-spacing:.2px}
.site-header .btn{left:982px;top:32px;width:122px;height:40px}

/* hero */
.hero{position:absolute;top:102px;left:0;width:1200px;height:558px;background:linear-gradient(100deg,#0d2a44 0%,#1a4a6e 40%,#3b7bb3 65%,#8cb8db 100%)}
.hero h1{position:absolute;left:142px;top:108px;width:520px;color:#fff;font-size:39px;line-height:51px;font-weight:700}
.hero p{position:absolute;left:142px;top:324px;width:420px;color:#fff;font-size:14px;line-height:25px}
.hero .btn{left:142px;top:403px;width:184px;height:40px}
.scroll-cue{position:absolute;left:564px;top:624px;width:72px;height:72px;border-radius:50%;background:#fff;display:flex;align-items:center;justify-content:center;box-shadow:0 4px 14px rgba(0,0,0,.12)}

/* section labels */
.eyebrow{position:absolute;left:0;width:1200px;text-align:center;font-size:12px;font-weight:600;letter-spacing:.5px;display:flex;justify-content:center;align-items:center;gap:8px}
.eyebrow i{width:12px;height:12px;border-radius:50%;border:3px solid var(--orange)}
.section-title{position:absolute;left:0;width:1200px;text-align:center;font-size:26px;font-weight:600}
.section-title em{font-style:normal;color:var(--orange)}

/* about */
.about-visual{left:115px;top:747px;width:520px;height:428px;background:radial-gradient(circle at 50% 50%,#b9b4ad 0%,#8c8782 40%,#e9e8e6 72%,#fff 80%);border-radius:50%}
.about-thumb{left:327px;top:1203px;width:123px;height:54px;background:linear-gradient(90deg,#9c9a97,#c9c7c3)}
.about-copy{left:641px;top:776px;width:430px}
.about-copy .kicker{color:var(--orange);font-size:16px;font-weight:500}
.about-copy h2{font-size:34px;font-weight:700;margin-top:4px;margin-bottom:18px}
.about-copy p{font-size:11.5px;line-height:22px;color:#3a424b;margin-bottom:15px}
.about-copy .btn{position:static;width:124px;height:40px;margin-top:2px}

/* services */
.services{left:0;top:1359px;width:1200px;height:605px;background:var(--mist)}
.service-card{position:absolute;top:1523px;width:282px;height:351px;background:#fff;border:1px solid var(--line);border-radius:4px;overflow:hidden}
.service-card .photo{height:162px}
.service-card h3{font-family:"Poppins",sans-serif;font-size:14px;font-weight:600;margin:18px 15px 10px}
.service-card p{font-size:11.5px;line-height:22px;color:var(--muted);margin:0 15px}
.service-card a{position:absolute;left:15px;bottom:20px;font-size:11.5px;font-weight:500;color:var(--ink);text-decoration:underline;display:flex;gap:8px;align-items:center}

/* why */
.why-item{position:absolute;width:260px}
.why-item h4{font-family:"Poppins",sans-serif;font-size:14px;font-weight:600;margin-bottom:6px}
.why-item p{font-size:11.5px;line-height:21px;color:var(--muted)}
.why-item.left{text-align:right}
.why-icon{position:absolute;width:56px;height:56px;border-radius:50%;display:flex;align-items:center;justify-content:center}
.why-icon.orange{background:var(--orange)}
.why-icon.dark{background:var(--navy)}
.hub{left:465px;top:2168px;width:270px;height:270px;border-radius:50%;background:#fff;box-shadow:0 6px 28px rgba(0,0,0,.1)}
.hub-ring{position:absolute;inset:18px;border-radius:50%;border:2px dashed var(--navy);display:flex;align-items:center;justify-content:center;flex-direction:column;gap:10px}
.hub .wordmark{font-size:30px}

/* trusted */
.trusted{left:0;top:2610px;width:1200px;height:548px;background:var(--navy);clip-path:polygon(0 7%,100% 0,100% 100%,0 100%)}
.trusted-copy{left:144px;top:2724px;width:470px;color:#fff}
.trusted-copy .label{font-size:12px;font-weight:600;display:flex;gap:8px;align-items:center}
.trusted-copy .label i{width:12px;height:12px;border-radius:50%;border:3px solid var(--orange)}
.trusted-copy h2{font-size:26px;font-weight:600;margin:12px 0 14px}
.trusted-copy h2 em{font-style:normal;color:var(--orange)}
.trusted-copy p{font-size:11.5px;line-height:23px;color:#d6dbe0;margin-bottom:16px}
.trusted-copy .btn{position:static;width:203px;height:40px;margin-top:28px}
.trusted-photo{left:641px;top:2721px;width:414px;height:345px;background:linear-gradient(135deg,#e7ebef,#a7b0ba 60%,#5c6773);border-radius:4px}

/* testimonials */
.review{position:absolute;top:3351px;width:282px;height:289px;background:#fff;border-radius:4px;box-shadow:0 4px 22px rgba(0,0,0,.08);padding:0 22px}
.review .quote{position:absolute;left:22px;top:-10px;width:40px;height:40px;border-radius:50%;background:var(--navy);color:#fff;font-family:"Outfit",sans-serif;font-size:34px;line-height:50px;text-align:center}
.review .quote.hot{background:var(--orange)}
.review .stars{position:absolute;left:22px;top:42px;color:#f5b400;font-size:18px;letter-spacing:3px}
.review .badge{position:absolute;right:20px;top:43px;width:22px;height:22px;border-radius:50%;border:3px solid #4a86e8}
.review p{position:absolute;left:22px;top:88px;width:238px;font-size:11.5px;line-height:22px;color:#3a424b}
.review .rule{position:absolute;left:22px;top:214px;width:40px;height:2px;background:var(--orange)}
.review h4{position:absolute;left:22px;top:228px;font-family:"Poppins",sans-serif;font-size:13px;font-weight:600}
.review span{position:absolute;left:22px;top:252px;font-size:11.5px;color:#3a424b}
.slider-arrow{position:absolute;top:3489px;width:24px;height:24px;border-radius:50%;display:flex;align-items:center;justify-content:center}

/* contact */
.contact-band{left:0;top:3755px;width:1200px;height:370px;background:linear-gradient(180deg,#f7845c,var(--orange));clip-path:polygon(0 13%,100% 0,100% 88%,0 100%)}
.contact-card{left:142px;top:3886px;width:916px;height:534px;background:#fff;border-radius:4px;box-shadow:0 6px 30px rgba(0,0,0,.08)}
.field{position:absolute;height:47px;border:1px solid var(--line);border-radius:3px;display:flex;align-items:center;gap:12px;padding-left:14px;font-size:12px;color:#6d757e}
.field .sep{width:1px;height:20px;background:var(--line)}
.field.tall{align-items:flex-start;padding-top:14px}
.submit{position:absolute;left:262px;top:4304px;width:676px;height:48px;background:var(--navy);color:#fff;font-size:12px;font-weight:500;display:flex;align-items:center;justify-content:center;gap:8px;border-radius:3px}

/* footer */
.footer-wedge{left:0;top:4506px;width:1200px;height:80px;background:var(--orange);clip-path:polygon(0 0,100% 100%,0 100%)}
.site-footer{left:0;top:4560px;width:1200px;height:399px;background:var(--navy-deep);clip-path:polygon(0 6%,100% 6%,100% 100%,0 100%)}
.site-footer .wordmark{position:absolute;left:142px;top:96px;color:#fff;font-size:30px}
.footer-about{position:absolute;left:142px;top:154px;width:220px;font-size:11.5px;line-height:20px;color:#d4d9de}
.follow{position:absolute;left:142px;top:232px;display:flex;gap:8px;align-items:center;font-size:11.5px;color:#d4d9de}
.follow b{width:20px;height:20px;border-radius:50%;border:1px solid #8a95a0}
.follow b.hot{background:var(--orange);border-color:var(--orange)}
.footer-col{position:absolute;top:98px}
.footer-col h4{font-family:"Poppins",sans-serif;color:#fff;font-size:14px;font-weight:500;margin-bottom:10px}
.footer-col h4::after{content:"";display:block;width:36px;height:2px;background:var(--orange);margin-top:6px}
.footer-col li{list-style:none;font-size:11.5px;color:#d4d9de;line-height:29px}
.footer-col li::before{content:"› ";color:var(--orange)}
.contact-line{display:flex;gap:14px;align-items:center;font-size:11.5px;color:#d4d9de;line-height:20px;margin-bottom:16px}
.contact-line .ic{flex:none;width:30px;height:30px;border-radius:50%;background:#33424f;display:flex;align-items:center;justify-content:center}
.contact-line .ic.hot{background:var(--orange)}
.copyright{position:absolute;left:0;top:366px;width:1200px;text-align:center;font-size:10.5px;color:#c3c9cf}
</style>
</head>
<body>

<header class="site-header">
  <div class="wordmark"><span class="dot"></span>Marlowe Group</div>
  <nav class="main-nav"><span>HOME</span><span>COMMERCIAL/INDUSTRIAL</span><span>RESIDENTIAL</span><span>BUSINESS SALES</span><span>ABOUT US</span><span>INFO ▾</span></nav>
  <a class="btn">CONTACT US</a>
</header>

<section class="hero" role="img" aria-label="Modern glass office towers beside a waterfront promenade">
  <h1>Specialists in Commercial/ Industrial Property, Trusted in Residential Property</h1>
  <p>Maximising returns, protecting investments, expert property advisory</p>
  <a class="btn">BOOK AN APPRAISAL</a>
</section>
<div class="scroll-cue"><svg width="16" height="16" viewBox="0 0 16 16" fill="none" stroke="#263440" stroke-width="1.6"><path d="M4 3l4 4 4-4M4 8l4 4 4-4"/></svg></div>

<div class="abs about-visual" role="img" aria-label="Team of colleagues gathered around a tablet, seen from above"></div>
<div class="abs about-thumb" role="img" aria-label="Textured floor detail"></div>
<div class="abs about-copy">
  <div class="kicker">WHO WE ARE</div>
  <h2>MARLOWE GROUP</h2>
  <p>At Marlowe Group, we are recognised as a trusted authority in commercial and residential property management, sales, and leasing. Property owners, investors, and developers turn to us for our proven expertise, discretion, and consistent results.</p>
  <p>Our mission is to set the standard for excellence in property services. Guided by innovation, integrity, and strategic execution, we deliver outcomes that protect assets, maximise returns, and create enduring value for our clients.</p>
  <p>Whether your goal is to manage your investment, increase rental income, lease to the right tenants, or achieve a successful sale, we provide clarity, confidence, &amp; tailored solutions at every stage of the journey.</p>
  <a class="btn">READ MORE</a>
</div>

<section class="abs services"></section>
<div class="eyebrow" style="top:1433px"><i></i>WHAT WE DO</div>
<h2 class="section-title" style="top:1460px">Property Management, <em>Sales &amp; Leasing</em></h2>
<article class="service-card" style="left:142px">
  <div class="photo" role="img" aria-label="Modern commercial building with paved forecourt" style="background:linear-gradient(160deg,#6c8aa8,#2e4257 60%,#9aa3a8)"></div>
  <h3>Commercial &amp; Industrial</h3>
  <p>Specialist management and leasing of premium commercial and industrial assets, trusted by investors and developers.</p>
  <a>Learn More <svg width="18" height="8" viewBox="0 0 18 8" fill="none" stroke="#ef532a" stroke-width="1.4"><path d="M0 4h16M13 1l3 3-3 3"/></svg></a>
</article>
<article class="service-card" style="left:458px">
  <div class="photo" role="img" aria-label="Two-storey family home with front lawn" style="background:linear-gradient(180deg,#5d8fd0 0%,#9fc0e6 40%,#c9b9a0 65%,#4f7a3a 100%)"></div>
  <h3>Residential Property</h3>
  <p>Expert residential property management and sales services with proven results and exceptional client outcomes.</p>
  <a>Learn More <svg width="18" height="8" viewBox="0 0 18 8" fill="none" stroke="#ef532a" stroke-width="1.4"><path d="M0 4h16M13 1l3 3-3 3"/></svg></a>
</article>
<article class="service-card" style="left:776px">
  <div class="photo" role="img" aria-label="Advisors meeting over a laptop in an office" style="background:linear-gradient(150deg,#cfd6dc,#7f8a94 55%,#3c4650)"></div>
  <h3>Property Advisory</h3>
  <p>Comprehensive financial reporting, budgeting, and expense management to optimize cash flow and returns.</p>
  <a>Learn More <svg width="18" height="8" viewBox="0 0 18 8" fill="none" stroke="#ef532a" stroke-width="1.4"><path d="M0 4h16M13 1l3 3-3 3"/></svg></a>
</article>

<div class="eyebrow" style="top:2074px"><i></i>WHY CHOOSE US</div>
<h2 class="section-title" style="top:2100px">Commercial &amp; Industrial Property <em>Management &amp; Leasing</em></h2>
<div class="abs hub"><div class="hub-ring"><span style="width:30px;height:30px;border-radius:50%;background:var(--orange)"></span><div class="wordmark">Marlowe</div></div></div>

<div class="why-item left" style="left:121px;top:2186px"><h4>Sector Expertise</h4><p>Deep knowledge across medical, healthcare, franchise, retail, and industrial sectors, enabling tailored strategies for each asset class.</p></div>
<div class="why-icon orange" style="left:399px;top:2196px"><svg width="26" height="26" viewBox="0 0 24 24" fill="none" stroke="#fff" stroke-width="1.6"><circle cx="12" cy="12" r="10"/><path d="M12 6l1.8 3.8 4 .5-3 2.8.8 4-3.6-2-3.6 2 .8-4-3-2.8 4-.5z"/></svg></div>
<div class="why-item left" style="left:121px;top:2349px"><h4>Proactive Asset Management</h4><p>Beyond operations, we actively enhance value, mitigate risk, and secure the right tenants.</p></div>
<div class="why-icon dark" style="left:399px;top:2360px"><svg width="26" height="26" viewBox="0 0 24 24" fill="none" stroke="#fff" stroke-width="1.6"><path d="M4 20l6-6M9 9l6 6M12 4l8 8-3 3-8-8z"/></svg></div>
<div class="why-icon dark" style="left:744px;top:2196px"><svg width="26" height="26" viewBox="0 0 24 24" fill="none" stroke="#fff" stroke-width="1.6"><circle cx="12" cy="12" r="3.5"/><path d="M12 2v4M12 18v4M2 12h4M18 12h4M4.9 4.9l2.8 2.8M16.3 16.3l2.8 2.8M4.9 19.1l2.8-2.8M16.3 7.7l2.8-2.8"/></svg></div>
<div class="why-item" style="left:820px;top:2186px"><h4>Bespoke Solutions</h4><p>Every property is unique. We craft customised management and leasing strategies aligned with your objectives and market conditions.</p></div>
<div class="why-icon orange" style="left:744px;top:2360px"><svg width="26" height="26" viewBox="0 0 24 24" fill="none" stroke="#fff" stroke-width="1.6"><path d="M3 11h4v9H3zM7 11l4-8c2 0 2.5 1.5 2 3.5L12.5 9H19a2 2 0 012 2.3l-1.3 6.8A2 2 0 0117.7 20H7"/></svg></div>
<div class="why-item" style="left:820px;top:2349px"><h4>Professional Excellence</h4><p>Integrity, precision, and industry-leading best</p></div>
<a class="btn" style="left:498px;top:2478px;width:203px;height:44px;font-size:13px">Book an Appraisal <svg width="12" height="12" viewBox="0 0 12 12" fill="none" stroke="#fff" stroke-width="1.5"><path d="M2 10L10 2M4 2h6v6"/></svg></a>

<section class="abs trusted"></section>
<div class="abs trusted-copy">
  <div class="label"><i></i>WHO WE ARE</div>
  <h2>We Are Recognised As <em>A Trusted</em></h2>
  <p>At Marlowe Group, we are recognised as a trusted authority in commercial and residential property management, sales, and leasing. Property owners, investors, and developers turn to us for our proven expertise, discretion, and consistent results.</p>
  <p>Our mission is to set the standard for excellence in property services. Guided by innovation, integrity, and strategic execution, we deliver outcomes that protect assets, maximise returns, and create enduring value for our clients.</p>
  <a class="btn">Schedule Consultation <svg width="12" height="12" viewBox="0 0 12 12" fill="none" stroke="#fff" stroke-width="1.5"><path d="M2 10L10 2M4 2h6v6"/></svg></a>
</div>
<div class="abs trusted-photo" role="img" aria-label="Presenter leading a meeting at a whiteboard with colleagues seated"></div>

<div class="eyebrow" style="top:3253px"><i></i>TESTIMONIALS</div>
<h2 class="section-title" style="top:3280px">What Our Clients Say <em>About Us</em></h2>
<div class="slider-arrow" style="left:89px;background:#cfd3d7"><svg width="10" height="10" viewBox="0 0 10 10" fill="none" stroke="#fff" stroke-width="1.6"><path d="M6.5 1.5L3 5l3.5 3.5"/></svg></div>
<div class="slider-arrow" style="left:1087px;background:var(--navy)"><svg width="10" height="10" viewBox="0 0 10 10" fill="none" stroke="#fff" stroke-width="1.6"><path d="M3.5 1.5L7 5 3.5 8.5"/></svg></div>
<article class="review" style="left:142px"><div class="quote">“</div><div class="stars">★★★★★</div><div class="badge"></div><p>“Sed ut perspiciatis unde omnis iste natus error sit voluptatem accusantium laudantium, totam rem aperiam, eaque ipsa quae ab illo inventore veritatis architect”</p><div class="rule"></div><h4>Owen Larkin</h4><span>Asset Portfolio Manager</span></article>
<article class="review" style="left:458px"><div class="quote hot">“</div><div class="stars">★★★★★</div><div class="badge"></div><p>“Sed ut perspiciatis unde omnis iste natus error sit voluptatem accusantium laudantium, totam rem aperiam, eaque ipsa quae ab illo inventore veritatis architect”</p><div class="rule"></div><h4>Clara Whitby</h4><span>Senior Leasing Specialist</span></article>
<article class="review" style="left:776px"><div class="quote">“</div><div class="stars">★★★★★</div><div class="badge"></div><p>“Sed ut perspiciatis unde omnis iste natus error sit voluptatem accusantium laudantium, totam rem aperiam, eaque ipsa quae ab illo inventore veritatis architect”</p><div class="rule"></div><h4>Daniel Osei</h4><span>Regional Property Director</span></article>
<svg class="abs" style="left:568px;top:3671px" width="64" height="8"><circle cx="4" cy="4" r="3" fill="#cfd3d7"/><circle cx="20" cy="4" r="3.5" fill="#ef532a"/><circle cx="36" cy="4" r="3" fill="#cfd3d7"/><circle cx="52" cy="4" r="3" fill="#cfd3d7"/></svg>

<div class="abs contact-band"></div>
<section class="abs contact-card"></section>
<div class="eyebrow" style="top:3956px"><i></i>CONTACT US</div>
<h2 class="section-title" style="top:3985px;font-size:24px">Ready To Discuss Your <em>Property Goals?</em></h2>
<div class="field" style="left:262px;top:4046px;width:329px"><svg width="14" height="14" viewBox="0 0 14 14" fill="none" stroke="#9aa1a8"><circle cx="7" cy="4.5" r="3"/><path d="M1.5 13c0-3 2.5-5 5.5-5s5.5 2 5.5 5"/></svg><span class="sep"></span>First Name</div>
<div class="field" style="left:609px;top:4046px;width:329px"><svg width="14" height="14" viewBox="0 0 14 14" fill="none" stroke="#9aa1a8"><circle cx="7" cy="4.5" r="3"/><path d="M1.5 13c0-3 2.5-5 5.5-5s5.5 2 5.5 5"/></svg><span class="sep"></span>Last Name</div>
<div class="field" style="left:262px;top:4108px;width:329px"><svg width="14" height="14" viewBox="0 0 14 14" fill="none" stroke="#9aa1a8"><rect x="1" y="3" width="12" height="9" rx="1"/><path d="M1 3l6 5 6-5"/></svg><span class="sep"></span>Your Email</div>
<div class="field" style="left:609px;top:4108px;width:329px"><svg width="14" height="14" viewBox="0 0 14 14" fill="none" stroke="#9aa1a8"><path d="M3 1l2.5 3-1.5 1.5c.8 1.8 2.2 3.2 4 4L9.5 8l3 2.5L11 13C6 12.5 1.5 8 1 3z"/></svg><span class="sep"></span>Phone</div>
<div class="field tall" style="left:262px;top:4171px;width:676px;height:100px"><svg width="14" height="14" viewBox="0 0 14 14" fill="none" stroke="#9aa1a8"><circle cx="7" cy="7" r="5.5"/><path d="M4.5 7h5"/></svg><span class="sep"></span>Your Message</div>
<div class="submit">Submit Now <svg width="12" height="12" viewBox="0 0 12 12" fill="none" stroke="#fff" stroke-width="1.5"><path d="M2 10L10 2M4 2h6v6"/></svg></div>

<div class="abs footer-wedge"></div>
<footer class="abs site-footer">
  <div class="wordmark"><span class="dot"></span>Marlowe</div>
  <p class="footer-about">Sed ut perspiciatis unde omnis iste natus error sit voluptatem accusantium dolorem.</p>
  <div class="follow">Follow Us: <b></b><b class="hot"></b><b></b></div>
  <div class="footer-col" style="left:418px"><h4>Quick Links</h4><ul><li>Home</li><li>Commercial / Industrial</li><li>Residential</li><li>Business Sales ⌄</li><li>About Us</li><li>Contact us</li></ul></div>
  <div class="footer-col" style="left:651px"><h4>Key Offerings</h4><ul><li>Business listings</li><li>Appraisal report</li><li>What we do</li><li>Who we are</li></ul></div>
  <div class="footer-col" style="left:838px;width:230px"><h4>Contact Us</h4>
    <div class="contact-line"><span class="ic"><svg width="12" height="14" viewBox="0 0 12 14" fill="none" stroke="#fff"><path d="M6 13s5-4.5 5-8A5 5 0 001 5c0 3.5 5 8 5 8z"/><circle cx="6" cy="5" r="1.8"/></svg></span>123, Lorem ipsum, dolor sit amet, adipiscing elit, 45</div>
    <div class="contact-line"><span class="ic hot"><svg width="13" height="13" viewBox="0 0 14 14" fill="none" stroke="#fff"><path d="M3 1l2.5 3-1.5 1.5c.8 1.8 2.2 3.2 4 4L9.5 8l3 2.5L11 13C6 12.5 1.5 8 1 3z"/></svg></span>Phone: (123) 456 7890</div>
    <div class="contact-line"><span class="ic"><svg width="13" height="13" viewBox="0 0 14 14" fill="none" stroke="#fff"><rect x="1" y="3" width="12" height="9" rx="1"/><path d="M1 3l6 5 6-5"/></svg></span>info@marlowegroup.com.au</div>
  </div>
  <div class="copyright">© 2023 Marlowe Business Sales. All Rights Reserved.</div>
</footer>

</body>
</html>
```